Zelvo Stationary

Design the stationary of Zelvo Promotions Group.

Zelvo is a BTL company, BTL meaning "below the line". In other words Zelvo is a Promotional Marketing company (the company that design the brands promotional activities).

The design should transmit creativity, agility, boldness.

I need:
* Bis Card
* Letter head
* Envelopes, both vertical and horizontal (for legal size), and letter envelope
* Folders
* PPT template (Title page and regular page)
* CD slip (CD envelope)
* ID card (employee card)

And what ever else you want to throw in.
Updates

Guys,

Something I missed from the brief.   The predominat color should be RED.

Also, have fun and play with the exclamation mark (!) of the logo. 

Hi guys, more comments:

Remember that Zelvo is a "creativity" agency, not in the advertising side but on the promotional side, and that should reflect on the stationary.

 I want a bold design.  Bold and yet crisp.

 

Guys, i just uploaded the Logo in AI format.

I Also uploaded the actual Zelvo Bis Card, wich I like.  So I will like to see some designs with that bis card approach.

Guys, I am so sorry, but I notice in your last post that I upladed a wrong design ("13154_promotions_group_zelvo_brief225630.ai").  The problem was that I asked the designer the file in AI format and he send me thw wrong file, and since I dont have Illustrator I could not verify it.

The differences are minor, I just already ask him the correct one (similar to the EPS file).

Sorry                                   

Just post the correct AI file : "Zelvo Logo.ai"

Reason: I'm expecting more designs to choose from and also I wont be available tomorrow to decide.

Reason: Sorry guys, but we are not there yet!

Target Market(s)

Marketing directors, Marketing Managers

Industry/Entity Type

Legal

Requirements
Must have
• Must work with the logo attached.
The predominat color should be RED.
Play and have fun with the exclamation mark (!).
Should not have
• * No old fonts

Should not be:
* boring
* Informal
* rigid

```html
<!DOCTYPE html>
<html lang="en">
<head>
<meta charset="utf-8">
<title>Zelvo Promotions Group – Business Card</title>
<link rel="stylesheet" href="https://fonts.googleapis.com/css2?family=Audiowide&family=Montserrat:wght@400;800&display=swap">
<style>
  :root {
    --canvas: #ffffff;
    --black: #000000;
    --charcoal: #3d3b3b;
    --red: #d8261b;
    --red-deep: #a81e1e;
    --grey-soft: #4a4a4a;
    --text-grey: #a9a9a9;
    --white: #ffffff;
  }
  * { box-sizing: border-box; }
  html, body {
    margin: 0;
    padding: 0;
    width: 1200px;
    height: 888px;
    overflow: hidden;
    background: var(--canvas);
  }
  .stage { position: relative; width: 1200px; height: 888px; }

  .card {
    position: absolute;
    top: 115px;
    width: 510px;
    height: 745px;
    border-radius: 18px;
    overflow: hidden;
  }
  .card--back { left: 74px; background: var(--black); }
  .card--front { left: 618px; background: var(--charcoal); }

  /* Back */
  .back-texture {
    position: absolute;
    left: 0; top: 0;
    width: 510px; height: 392px;
    background: linear-gradient(160deg, #1c1c1c 0%, #000000 45%, #141414 75%, #000000 100%);
  }
  .back-panel {
    position: absolute;
    left: 0; top: 392px;
    width: 510px; height: 306px;
    background: linear-gradient(165deg, #e0412f 0%, var(--red) 40%, #c72118 70%, #d8372a 100%);
  }
  .contact-list {
    position: absolute;
    left: 10px; top: 226px;
    margin: 0; padding: 0;
    list-style: none;
  }
  .contact-item {
    display: flex;
    align-items: center;
    height: 36px;
    margin-bottom: 24px;
    font-family: "Montserrat", Arial, sans-serif;
    font-size: 17px;
    color: var(--text-grey);
  }
  .contact-item svg { width: 46px; height: 36px; margin-right: 14px; flex: none; }

  /* Wordmark */
  .wordmark {
    position: absolute;
    color: var(--black);
    font-family: "Montserrat", Arial, sans-serif;
    font-weight: 800;
  }
  .wordmark-row { display: flex; align-items: flex-end; }
  .wordmark-name { line-height: 0.8; letter-spacing: 1px; }
  .wordmark-dot {
    display: block;
    border-radius: 50%;
    background: var(--black);
  }
  .wordmark-sub { display: block; letter-spacing: 4px; line-height: 1; }

  .back-panel .wordmark { left: 44px; top: 142px; }
  .back-panel .wordmark-name { font-size: 60px; }
  .back-panel .wordmark-dot { width: 20px; height: 20px; margin-left: 10px; }
  .back-panel .wordmark-sub { font-size: 13px; margin-top: 10px; letter-spacing: 3.4px; }

  /* Front */
  .front-band {
    position: absolute;
    left: 0; width: 510px;
    background: var(--red-deep);
  }
  .front-band--top { top: 31px; height: 19px; }
  .front-band--bottom { top: 677px; height: 52px; opacity: 0.9; }
  .front-ribbons {
    position: absolute;
    left: 0; top: 225px;
    width: 510px; height: 420px;
    background: linear-gradient(160deg, rgba(235,235,235,0.55) 0%, rgba(216,38,27,0.9) 35%, rgba(240,240,240,0.7) 55%, rgba(216,38,27,0.75) 75%, rgba(61,59,59,0) 100%);
    clip-path: polygon(0 5%, 100% 0, 100% 100%, 0 55%);
  }
  .holder-name {
    position: absolute;
    left: 79px; top: 108px;
    margin: 0;
    font-family: "Audiowide", sans-serif;
    font-weight: 400;
    font-size: 33px;
    letter-spacing: 3px;
    color: var(--black);
  }
  .holder-email {
    position: absolute;
    left: 67px; top: 152px;
    margin: 0;
    font-family: "Montserrat", Arial, sans-serif;
    font-size: 26px;
    letter-spacing: 0.6px;
    color: var(--text-grey);
  }
  .card--front .wordmark { left: 71px; top: 240px; }
  .card--front .wordmark-name { font-size: 64px; }
  .card--front .wordmark-dot { width: 22px; height: 22px; margin-left: 10px; }
  .card--front .wordmark-sub { font-size: 14px; margin-top: 10px; letter-spacing: 3.6px; }
</style>
</head>
<body>
<main class="stage">

  <section class="card card--back" aria-label="Card back">
    <div class="back-texture" role="img" aria-label="Fine grey flowing line pattern on black"></div>

    <ul class="contact-list">
      <li class="contact-item">
        <svg viewBox="0 0 46 36" aria-hidden="true"><rect x="2" y="5" width="42" height="26" fill="none" stroke="#a9a9a9" stroke-width="2"/><path d="M2 5 L23 22 L44 5" fill="none" stroke="#a9a9a9" stroke-width="2"/></svg>
        yourdesign@zelvo.com
      </li>
      <li class="contact-item">
        <svg viewBox="0 0 46 36" aria-hidden="true"><circle cx="23" cy="18" r="16" fill="none" stroke="#a9a9a9" stroke-width="2"/><ellipse cx="23" cy="18" rx="7" ry="16" fill="none" stroke="#a9a9a9" stroke-width="2"/><path d="M7 18 H39 M10 10 H36 M10 26 H36" stroke="#a9a9a9" stroke-width="2"/></svg>
        www.zelvo.com
      </li>
      <li class="contact-item">
        <svg viewBox="0 0 46 36" aria-hidden="true"><path d="M10 6 q-5 8 5 19 q10 10 18 6 l3-5 -7-6 -4 3 q-6-2 -9-9 l3-4 -5-8z" fill="none" stroke="#a9a9a9" stroke-width="2" stroke-linejoin="round"/></svg>
        0900-555-010-246
      </li>
    </ul>

    <div class="back-panel" role="img" aria-label="Red panel with pale flowing line pattern">
      <div class="wordmark">
        <span class="wordmark-row"><span class="wordmark-name">ZELVO</span><span class="wordmark-dot"></span></span>
        <span class="wordmark-sub">PROMOTIONS GROUP</span>
      </div>
    </div>
  </section>

  <section class="card card--front" aria-label="Card front">
    <div class="front-band front-band--top"></div>
    <div class="front-ribbons" role="img" aria-label="Sweeping red, white and grey ribbon graphic"></div>
    <h1 class="holder-name">Mara Delgado</h1>
    <p class="holder-email">maradelgado@zelvo.com</p>
    <div class="wordmark">
      <span class="wordmark-row"><span class="wordmark-name">ZELVO</span><span class="wordmark-dot"></span></span>
      <span class="wordmark-sub">PROMOTIONS GROUP</span>
    </div>
    <div class="front-band front-band--bottom"></div>
  </section>

</main>
</body>
</html>
```